Refresh of far from plain IT company website

Our web site is starting to show it's age. You can see the existing site here: www.plumbwick.net. As a growing company we want to come across as a dynamic collection of IT experts.

We want to update the design so are open to any colour palette and look, but want to retain our current table logo. We use the logo on our business cards but with a white background - see the attached file, so you don't need to keep the brown or the green.

The design should consider the range of browsers that will be looking at the site - so please show how it will look on a wide screen laptop and a 768x1024 tablet.

We want to add some pages about our team and their skills, probably with photos of each person on the team.

This is an uncoded project - the PSD files of the design is required, not coding.
Updates

Thanks everyone for the submissions so far.  It's a holiday day in the UK today but we will get some feedback on the designs so far out to you.

Target Market(s)

Architects and other creative types looking for IT support

Industry/Entity Type

Business

Font styles to use
Serif
Sans Serif

Requirements
Must have
• Must look good on a laptop and an iPad.

```html
<!DOCTYPE html>
<html lang="en">
<head>
<meta charset="utf-8">
<title>plumbwick – IT support</title>
<link href="https://fonts.googleapis.com/css2?family=Open+Sans:wght@400;600;700&family=Kaushan+Script&display=swap" rel="stylesheet">
<style>
:root{
  --gold:#d9a80c;
  --plum:#8c1450;
  --ink:#333;
  --muted:#555;
  --light:#f1f1f1;
  --footer:#262626;
  --footer-deep:#1b1b1b;
  --line:#e2e2e2;
}
*{box-sizing:border-box;margin:0;padding:0}
html,body{width:802px;height:1200px;overflow:hidden;background:#fff}
body{font-family:"Open Sans",Arial,sans-serif;color:var(--ink);position:relative}
.abs{position:absolute}
a{color:inherit;text-decoration:none}

/* top bar */
.topbar{top:0;left:0;width:802px;height:19px;background:#f7f7f7;border-bottom:1px solid var(--line);font-size:8px;color:#555}
.topbar .contact{left:96px;top:4px;display:flex;gap:12px;align-items:center}
.topbar .contact span{display:flex;align-items:center;gap:5px}
.topbar .social{right:95px;top:4px;display:flex;gap:6px}
.topbar .social i{width:10px;height:10px;border-radius:50%;background:#9a9a9a;display:block}

/* header */
.header{top:19px;left:0;width:802px;height:46px;background:#fff}
.brand{left:94px;top:11px;display:flex;align-items:center;gap:8px}
.brand .mark{width:18px;height:18px;background:var(--gold)}
.brand .name{font-size:20px;font-weight:600;color:var(--plum);letter-spacing:-.3px}
.nav{right:95px;top:17px;display:flex;font-size:9.5px;color:#222}
.nav a{padding:0 8px;border-left:1px solid #999;line-height:10px}
.nav a:first-child{border-left:0;position:relative}
.nav a.active:after{content:"";position:absolute;left:8px;right:8px;top:16px;height:2px;background:var(--gold)}

/* hero */
.hero{top:65px;left:0;width:802px;height:293px;
  background:
   radial-gradient(ellipse 260px 200px at 330px 190px,rgba(214,110,50,.85),rgba(214,110,50,0) 70%),
   radial-gradient(ellipse 300px 260px at 120px 120px,rgba(140,22,70,.95),rgba(140,22,70,0) 80%),
   linear-gradient(90deg,#6a2452 0%,#7a2a3c 40%,#4f3a44 65%,#3c3b42 100%)}
.hero .label{font-family:"Kaushan Script",cursive;color:#fff;font-size:15px;line-height:1}
.hero .icon{border:2px solid rgba(255,255,255,.9);border-radius:50%;width:32px;height:32px}
.hero .badge{left:346px;top:118px;width:118px;height:33px;background:#fff;border-radius:3px;display:flex;align-items:center;justify-content:center;gap:6px}
.hero .badge .mark{width:12px;height:12px;background:var(--gold)}
.hero .badge .name{font-size:14px;font-weight:600;color:var(--plum)}
.hero .strap{left:0;bottom:0;width:802px;height:40px;background:rgba(40,20,35,.55);color:#fff;font-size:16.5px;text-align:center;line-height:40px}

/* tabs */
.tabs{top:358px;left:0;width:802px;height:46px;background:linear-gradient(#f9f9f9,#ececec);border-bottom:1px solid var(--line)}
.tab{top:0;height:46px;display:flex;align-items:center;gap:10px;font-size:12px;color:#222}
.tab.active{background:#fff;border:1px solid #ddd;border-bottom:0;height:47px;padding:0 27px 0 20px;box-shadow:0 -1px 3px rgba(0,0,0,.08)}
.tab svg{display:block}

/* welcome */
.welcome-title{top:431px;left:0;width:802px;text-align:center;font-size:23px;font-weight:400;color:var(--gold)}
.welcome-title b{color:var(--plum);font-weight:400}
.welcome-text{top:478px;left:95px;width:612px;text-align:center;font-size:10px;line-height:15.5px;color:#444}
.welcome-text b{color:var(--plum);font-weight:400}

/* features */
.band{top:554px;left:0;width:802px;height:178px;background:var(--light)}
.feature{top:528px;width:160px;text-align:center}
.feature .ring{width:51px;height:51px;border-radius:50%;background:#fff;margin:0 auto;display:flex;align-items:center;justify-content:center}
.feature h3{font-size:12px;font-weight:400;color:#222;margin-top:13px;letter-spacing:.2px}
.feature p{font-size:8px;line-height:11.5px;color:#444;margin-top:8px}
.feature .more{display:block;margin-top:8px;font-size:8.5px;text-decoration:underline}

/* testimonial */
.quote{top:732px;left:0;width:802px;height:136px;background:linear-gradient(90deg,#4a3a30,#5e5044 40%,#3e3f3c 70%,#4a4640)}
.quote .mark{left:0;width:802px;top:6px;text-align:center;font-size:44px;font-weight:700;color:#aaa;font-family:Georgia,serif;line-height:1}
.quote p{left:0;width:802px;top:44px;text-align:center;color:#fff;font-size:11.5px;line-height:16.5px}
.quote .avatar{left:282px;top:85px;width:40px;height:40px;border-radius:50%;background:linear-gradient(#c9b7a8,#8a6f5f);border:2px solid #fff;box-shadow:0 0 0 2px var(--plum)}
.quote .who{left:332px;top:98px;font-size:10.5px;font-weight:700;color:var(--gold)}
.quote .arrow{top:62px}

/* clients */
.clients{top:868px;left:0;width:802px;height:116px;background:#f4f4f4}
.clients h2{position:absolute;top:16px;left:0;width:802px;text-align:center;font-weight:400;font-size:23px;color:var(--gold)}
.clients h2 b{color:var(--plum);font-weight:400}
.client{top:70px;display:flex;align-items:center;gap:6px;font-size:18px;font-weight:600;color:#5a5a5a;white-space:nowrap}
.client i{width:12px;height:12px;border-radius:50%;background:#5a5a5a;display:block}

/* footer */
.footer{top:984px;left:0;width:802px;height:190px;background:var(--footer);color:#ddd}
.footer h4{position:absolute;top:20px;font-size:11.5px;font-weight:400;color:#fff;padding-bottom:8px;width:148px;border-bottom:1px solid #6b5a22}
.footer h4:after{content:"";position:absolute;left:0;bottom:-1px;width:52px;height:1px;background:var(--gold)}
.post{display:flex;gap:12px;align-items:center;font-size:7px;line-height:10px;color:#ddd}
.post .thumb{width:39px;height:26px;background:linear-gradient(135deg,#e8e2d6,#b59a78);border:1px solid #fff}
.tweet{display:flex;gap:10px;font-size:7px;line-height:10px}
.tweet .bird{width:15px;height:15px;border:1px solid #ddd;border-radius:50%;flex:none;margin-top:3px}
.tweet small{display:block;font-size:5.5px;color:#aaa;margin-top:4px}
.info{display:flex;gap:10px;font-size:7.5px;line-height:10.5px}
.bottom{top:1174px;left:0;width:802px;height:26px;background:var(--footer-deep);text-align:center;color:#ccc;font-size:8.5px;line-height:26px}
</style>
</head>
<body>

<div class="abs topbar">
  <div class="abs contact">
    <span><svg width="8" height="8" viewBox="0 0 10 10"><path d="M2 1l2 2-1 1.5c.6 1.2 1.4 2 2.5 2.5L7 6l2 2-1.5 1.5C4.5 9 1 5.5.5 2.5z" fill="#888"/></svg>020 7000 4812</span>
    <span><svg width="9" height="7" viewBox="0 0 10 7"><rect width="10" height="7" fill="#888"/><path d="M0 0l5 4 5-4" stroke="#f7f7f7" fill="none"/></svg>website@plumbwick.net</span>
  </div>
  <div class="abs social" aria-label="Social links"><i></i><i></i><i></i><i></i></div>
</div>

<header class="abs header">
  <div class="abs brand"><span class="mark"></span><span class="name">plumbwick</span></div>
  <nav class="abs nav">
    <a class="active" href="#">Home</a><a href="#">About us</a><a href="#">What we do</a><a href="#">News blog</a><a href="#">Articles</a><a href="#">Clients</a><a href="#">Partners</a>
  </nav>
</header>

<section class="abs hero" role="img" aria-label="Blurred office background in plum, orange and grey">
  <div class="abs label" style="left:350px;top:20px">Research based</div>
  <div class="abs icon" role="img" aria-label="Microscope icon" style="left:386px;top:54px"></div>
  <div class="abs label" style="left:195px;top:80px;line-height:.95">Briging<br>ideas</div>
  <div class="abs icon" role="img" aria-label="Brain icon" style="left:275px;top:118px"></div>
  <div class="abs badge"><span class="mark"></span><span class="name">plumbwick</span></div>
  <div class="abs label" style="left:503px;top:84px">Industry specific</div>
  <div class="abs icon" role="img" aria-label="Factory icon" style="left:498px;top:118px"></div>
  <div class="abs icon" role="img" aria-label="Pointing hand icon" style="left:388px;top:170px"></div>
  <div class="abs label" style="left:354px;top:230px">Solutions</div>
  <svg class="abs" style="left:0;top:0" width="802" height="293" fill="none" stroke="#fff" stroke-width="1" opacity=".8">
    <path d="M426 52c10 4 14 14 20 28M442 76l4 5 3-6"/>
    <path d="M238 112c0 14 6 22 20 24M252 132l6 4-6 3"/>
    <path d="M566 112c0 16-8 22-20 24M552 132l-6 4 6 3"/>
    <path d="M375 220c-10-8-12-18-8-30M363 195l4-6 4 5"/>
  </svg>
  <div class="abs strap">Provides a high quality, one-stop&nbsp; IT support solution for your business</div>
</section>

<div class="abs tabs">
  <div class="abs tab active" style="left:94px">
    <svg width="20" height="20" viewBox="0 0 20 20"><circle cx="10" cy="7" r="5" fill="#d9a80c"/><path d="M1 20c1-6 5-8 9-8s8 2 9 8z" fill="#d9a80c"/></svg>Support</div>
  <div class="abs tab" style="left:232px">
    <svg width="17" height="17" viewBox="0 0 18 18" fill="none" stroke="#222" stroke-width="2"><path d="M3 11V9a6 6 0 0112 0v2"/><rect x="2" y="10" width="3" height="5" fill="#222"/><rect x="13" y="10" width="3" height="5" fill="#222"/></svg>Consultancy</div>
  <div class="abs tab" style="left:380px">
    <svg width="16" height="16" viewBox="0 0 16 16"><circle cx="8" cy="8" r="7" fill="#888"/><path d="M8 1a7 7 0 000 14z" fill="#222"/></svg>CAD</div>
  <div class="abs tab" style="left:487px">
    <svg width="17" height="17" viewBox="0 0 18 18" fill="none" stroke="#222" stroke-width="2"><path d="M15 9a6 6 0 01-11 3M3 9a6 6 0 0111-3"/><path d="M14 2v4h-4M4 16v-4h4"/></svg>Hosting</div>
  <div class="abs tab" style="left:605px">
    <svg width="17" height="17" viewBox="0 0 18 18" fill="none" stroke="#222" stroke-width="1.6"><path d="M1 1v16h16"/><path d="M3 14l4-5 3 3 6-8"/></svg>Development</div>
</div>

<h1 class="abs welcome-title">Welcome to <b>plumbwick</b></h1>
<p class="abs welcome-text"><b>Plumbwick</b> was established with a specific aim: to consistently deliver an advanced and comprehensive IT service for ambitious growing companies across all industry sectors.</p>

<div class="abs band"></div>

<div class="abs feature" style="left:92px">
  <div class="ring" style="border:1px solid var(--gold)"><svg width="26" height="26" viewBox="0 0 20 20"><circle cx="10" cy="7" r="4.5" fill="#d9a80c"/><path d="M2 18c1-5 4-7 8-7s7 2 8 7z" fill="#d9a80c"/></svg></div>
  <h3>WHO WE ARE ?</h3>
  <p>Plumbwick was established with a specific aim: to consistently deliver an advanced and comprehensive IT service for ambitious growing companies across many industry sectors. We aim to provide the very best in service and support, and to aid business</p>
  <a class="more" style="color:var(--gold)" href="#">more</a>
</div>
<div class="abs feature" style="left:306px">
  <div class="ring" style="border:1px solid var(--plum)"><svg width="26" height="26" viewBox="0 0 20 20"><circle cx="10" cy="10" r="8" fill="#8c1450"/><path d="M6 6l3 1 1 3-2 2 1 3-3-2zM12 5l3 2-1 3-2-1z" fill="#fff"/></svg></div>
  <h3>Latest NEWS</h3>
  <p>Donec consectetur metus eget felis commodo, ut iaculis mi dignissim. Maecenas in suscipit libero, in dictum Donec consectetur metus eget felis commodo, ut iaculis mi dignissim. Maecenas in suscipit libero, in dictum metus</p>
  <a class="more" style="color:var(--plum)" href="#">more</a>
</div>
<div class="abs feature" style="left:548px">
  <div class="ring" style="border:1px solid #555"><svg width="26" height="26" viewBox="0 0 20 20"><path d="M3 10l5 5 9-10" fill="none" stroke="#444" stroke-width="3"/></svg></div>
  <h3 style="font-size:10.5px;margin-top:14px">WHY CHOOSE US ?</h3>
  <p>Donec consectetur metus eget felis commodo, ut iaculis mi dignissim. Maecenas in suscipit libero, in dictum Donec consectetur metus eget felis commodo, ut iaculis mi dignissim. Maecenas in suscipit libero, in dictum metus</p>
  <a class="more" style="color:#666" href="#">more</a>
</div>

<section class="abs quote" role="img" aria-label="Blurred photo of a desk with a laptop">
  <div class="abs mark">&ldquo;</div>
  <p class="abs">Vestibulum ante ipsum primis in faucibus orci luctus et ultrices posuere cubilia Curae;<br>Cras velit leo, laoreet sit amet lobortis vel.Stet clita kasd gubergren, no sea takimata</p>
  <div class="abs avatar" role="img" aria-label="Portrait of the quoted client"></div>
  <div class="abs who">- sanctus est dolor sit amet</div>
  <svg class="abs arrow" style="left:94px" width="10" height="14" viewBox="0 0 10 14"><path d="M8 1L2 7l6 6" fill="none" stroke="#fff" stroke-width="2"/></svg>
  <svg class="abs arrow" style="left:698px" width="10" height="14" viewBox="0 0 10 14"><path d="M2 1l6 6-6 6" fill="none" stroke="#fff" stroke-width="2"/></svg>
</section>

<section class="abs clients">
  <h2>Our <b>Clients</b></h2>
  <div class="abs client" style="left:104px">Quillmere</div>
  <div class="abs client" style="left:240px"><i></i>Harthollow</div>
  <div class="abs client" style="left:370px">Fennick</div>
  <div class="abs client" style="left:460px"><i></i>Drovemark</div>
  <div class="abs client" style="left:612px"><i></i>Tallowby</div>
</section>

<footer class="abs footer">
  <h4 style="left:93px">RECENT POSTS</h4>
  <div class="abs" style="left:93px;top:64px;display:flex;flex-direction:column;gap:13px">
    <div class="post"><div class="thumb" role="img" aria-label="Blog post thumbnail"></div><div>Post with slide entry<br>April 8, 2014</div></div>
    <div class="post"><div class="thumb" role="img" aria-label="Blog post thumbnail"></div><div>Post with slide entry<br>April 8, 2014</div></div>
    <div class="post"><div class="thumb" role="img" aria-label="Blog post thumbnail"></div><div>Post with slide entry<br>April 8, 2014</div></div>
  </div>

  <h4 style="left:313px">RECENT TWEETS</h4>
  <div class="abs" style="left:313px;top:64px;display:flex;flex-direction:column;gap:9px;width:190px">
    <div class="tweet"><span class="bird"></span><div>Donec earum rerum hic tenetur ans sapiente delectus, ut aut reiciendise<small>about 14 hours ago</small></div></div>
    <div class="tweet"><span class="bird"></span><div>Donec earum rerum hic tenetur ans sapiente delectus, ut aut reiciendise<small>about 14 hours ago</small></div></div>
    <div class="tweet"><span class="bird"></span><div>Donec earum rerum hic tenetur ans sapiente delectus, ut aut reiciendise<small>about 14 hours ago</small></div></div>
  </div>

  <h4 style="left:562px;width:146px">CONTACT INFORMATION</h4>
  <div class="abs info" style="left:562px;top:66px">
    <svg width="8" height="11" viewBox="0 0 8 11"><path d="M4 0a4 4 0 014 4c0 3-4 7-4 7S0 7 0 4a4 4 0 014-4z" fill="#ddd"/><circle cx="4" cy="4" r="1.5" fill="#262626"/></svg>
    <div>Plumbwick.net Ltd Larch House<br>48-52 Mill Lane London<br>N1 4QT<br>United Kingdom</div>
  </div>
  <div class="abs info" style="left:562px;top:126px;font-weight:700">
    <svg width="8" height="9" viewBox="0 0 10 10"><path d="M2 1l2 2-1 1.5c.6 1.2 1.4 2 2.5 2.5L7 6l2 2-1.5 1.5C4.5 9 1 5.5.5 2.5z" fill="#ddd"/></svg>020 7000 4812</div>
  <div class="abs info" style="left:562px;top:147px">
    <svg width="9" height="7" viewBox="0 0 10 7"><rect width="10" height="7" fill="#ddd"/><path d="M0 0l5 4 5-4" stroke="#262626" fill="none"/></svg>website@plumbwick.net</div>
</footer>

<div class="abs bottom">&copy; 2014 plumbwick. All right reserved.</div>

</body>
</html>
```